Business card for marketing analytics company

Need a business card for new company. I have a logo already that I want to be built into the card and should use those colours

Company is called steered by tallies
Design must bring steered by tallies to life not be a card that could be for anyone with a logo put on it.

Like the front to be fairly clean and uncluttered bringing the logo out with a suitable design on the back of the card.

The logo represents a compass and business growth so those themes along with numbers, analytics , data are appropriate.
I'm often working with creative industries so also needs to reflect the creative side of analytics rather than be very corporate looking.

Target Market(s)

Ad agency, media agency, consumer goods clients

Industry/Entity Type

Market Research

Contact Information for Business Card

Needs to include name, title, email and phone number

Colors
f78f20
f68d4d
ec1f27

Requirements
Must have
• Must bring steered by tallies to life not be a card that could be for anyone with a logo put on it.
• Logo, Correct colours
• Like a design on the back that relates to company name
• Designs for both sides
Should not have
• Please do not just submit logo and a coloured card.
• It needs to have a design element to it
• No black background
• No clear cards - needs front & back

```html
<!DOCTYPE html>
<html lang="en">
<head>
<meta charset="utf-8">
<title>Steered by Tallies — Business Card</title>
<link rel="stylesheet" href="https://fonts.googleapis.com/css2?family=Source+Sans+3:wght@400;600;700&display=swap">
<style>
  :root {
    --stage: #2b2b2b;
    --brand-orange: #f47524;
    --brand-red: #c8202a;
    --card-white: #ffffff;
    --ink-light: #ffffff;
  }
  * { margin: 0; padding: 0; box-sizing: border-box; }
  html, body {
    width: 1200px;
    height: 987px;
    overflow: hidden;
    background: var(--stage);
    font-family: "Source Sans 3", Arial, sans-serif;
  }
  .canvas {
    position: relative;
    width: 1200px;
    height: 987px;
  }
  .card {
    position: absolute;
    width: 615px;
    height: 350px;
    border-radius: 21px;
    overflow: hidden;
    background: var(--card-white);
  }
  .card--front { left: 293px; top: 130px; }
  .card--back  { left: 292px; top: 506px; }

  .front-field {
    position: absolute;
    inset: 0;
    width: 100%;
    height: 100%;
  }
  .holder {
    position: absolute;
    left: 39px;
    top: 34px;
    color: var(--ink-light);
  }
  .holder__name {
    font-size: 20px;
    font-weight: 700;
    letter-spacing: 0.2px;
    line-height: 1.1;
  }
  .holder__title {
    font-size: 15px;
    font-weight: 400;
    line-height: 1.3;
  }
  .contact {
    position: absolute;
    left: 39px;
    top: 240px;
    list-style: none;
    color: var(--ink-light);
    font-size: 15px;
    line-height: 23.5px;
  }
  .contact__item {
    display: flex;
    align-items: center;
    gap: 8px;
  }
  .contact__icon {
    width: 15px;
    height: 15px;
    flex: none;
  }
  .front-brand {
    position: absolute;
    left: 320px;
    top: 0;
    width: 295px;
    height: 330px;
    display: flex;
    flex-direction: column;
    justify-content: center;
    align-items: center;
    text-align: center;
    color: var(--brand-orange);
    font-size: 34px;
    font-weight: 600;
    line-height: 1.1;
  }
  .back-brand {
    position: absolute;
    left: 130px;
    top: 117px;
    display: flex;
    align-items: center;
    gap: 22px;
  }
  .back-brand__dot {
    width: 112px;
    height: 112px;
    border-radius: 50%;
    border: 4px solid var(--brand-red);
    flex: none;
  }
  .back-brand__name {
    color: var(--brand-orange);
    font-size: 32px;
    font-weight: 600;
    line-height: 1.05;
  }
</style>
</head>
<body>
<main class="canvas">

  <section class="card card--front" aria-label="Card front">
    <svg class="front-field" viewBox="0 0 615 350" aria-hidden="true">
      <rect width="615" height="350" fill="var(--brand-orange)"/>
      <circle cx="481" cy="165" r="190" fill="var(--card-white)"/>
      <rect x="481" y="0" width="134" height="350" fill="var(--card-white)"/>
    </svg>

    <div class="holder">
      <p class="holder__name">MARA QUINLAN</p>
      <p class="holder__title">CEO/Founder</p>
    </div>

    <ul class="contact">
      <li class="contact__item">
        <svg class="contact__icon" viewBox="0 0 16 16" aria-hidden="true">
          <path d="M3.5 1.5l2.5 0.5 1 3-1.6 1.3a9 9 0 0 0 4.3 4.3L11 9l3 1 .5 2.5-2 2C6.5 14.5 1.5 9.5 1.5 3.5z" fill="var(--ink-light)"/>
        </svg>
        555 210 4837
      </li>
      <li class="contact__item">
        <svg class="contact__icon" viewBox="0 0 16 16" aria-hidden="true">
          <rect x="1" y="3.5" width="14" height="9.5" fill="var(--ink-light)"/>
          <path d="M1.5 4l6.5 5 6.5-5" fill="none" stroke="var(--brand-orange)" stroke-width="1.3"/>
        </svg>
        mara@steeredbytallies.com
      </li>
      <li class="contact__item">
        <svg class="contact__icon" viewBox="0 0 16 16" aria-hidden="true">
          <circle cx="8" cy="8" r="7" fill="var(--ink-light)"/>
          <path d="M4 4.5c1.5.5 2 1.5 1.5 3S6 10 7 10.5M10 2.5c-.5 1.5 1 2 2 2.5s.5 2 1.5 2.5M9 13c0-1.5 1-2 2-2.5" fill="none" stroke="var(--brand-orange)" stroke-width="1.2"/>
        </svg>
        www.steeredbytallies.com
      </li>
    </ul>

    <p class="front-brand">Steered by<br>Tallies</p>
  </section>

  <section class="card card--back" aria-label="Card back">
    <div class="back-brand">
      <span class="back-brand__dot" aria-hidden="true"></span>
      <p class="back-brand__name">Steered by<br>Tallies</p>
    </div>
  </section>

</main>
</body>
</html>
```